Website Design Needed for Performance Horse Trading Business

We require a website designed for Saddlewend, a new business which lists top quality performance stock horse bloodlines for sale. Our Australian company caters to the Australian Stock Horse, Quarter Horse and Paint Horse breeds of horse used for performance events such as Camp drafting and Cutting. The website design needs to communicate quality, have a professional look while maintaining a western, rural feel.
Colour schemes that we are looking for are either grey and orange, navy and grey or brown and grey.
The logo for the website has been attached below
Design deliverables are as follows:
-Main Page
-Horses for Sale Page
-Horse Listing Page
-Html & CSS files for pages
MAIN PAGE
----------------
Description: This page is where customers land, search for horses, see premium horses
Elements which need to be included on the main page are
-a horse filter section, allowing customers to search for horse listings by filtering attributes.
-premium listings displaying large photos of horse, price and location.
Horses for Sale PAGE
---------------------------------
Description: This page displays a list of available horses for sale as per the filtered results.
Elements which need to be included on this page are
- a filter panel which allows customers to filter results
- list of horses available for sale
Horse Listing Page
-------------------------------
Description: This page displays all the information about the horse for sale.
Screenshots of the basic program are attached for the Horses for Sale Page and the Horse Listing Page to give an idea of the elements required ONLY and should not be thought of as a design guideline.
Webpage HEADER
-------------------------
The Header section of the website should include login/signup buttons, 'my account' buttons (or links) as well as a featured link/button that says 'Sell Your Horse'
Updates
Thank you all for your designs so far. We would like to see the Sell Your Horse section featured more in the website design to attract customers. This would be as a button or highlighted link that is eye catching in the primary section of the website design of the main page. Perhaps placing it on the right hand side adjacent to the search function lets customers make the mental decision as to whether they are looking to buy or looking to sell when they visit the website. The wording above or near the button would be 'Advertise your horse with us' with the words on the button being 'Create Ad!'.
Industry/Entity Type
Events
Look and feel
Each slider illustrates characteristics of the customer's brand and the style your logo design should communicate.

```html
<!DOCTYPE html>
<html lang="en">
<head>
<meta charset="utf-8">
<title>Saddlewend</title>
<link href="https://fonts.googleapis.com/css2?family=Open+Sans:wght@400;600;700&family=Roboto:wght@400;500&family=Didact+Gothic&display=swap" rel="stylesheet">
<style>
:root{
  --dark:#2a201d;
  --orange:#e48a12;
  --orange-light:#f0a02a;
  --text:#3a3a3a;
  --muted:#6b6b6b;
  --line:#dcdcdc;
  --white:#ffffff;
  --teal:#5b7b85;
}
*{margin:0;padding:0;box-sizing:border-box}
html,body{width:686px;height:1200px;overflow:hidden}
body{position:relative;background:var(--white);font-family:"Open Sans",sans-serif;color:var(--text)}
.abs{position:absolute}
/* header */
.site-header{left:0;top:0;width:686px;height:63px;background:var(--white)}
.brand{left:56px;top:14px;font-size:22px;font-weight:700;color:var(--dark);letter-spacing:1px;display:flex;align-items:center;gap:7px}
.brand-dot{width:10px;height:10px;border-radius:50%;background:var(--dark)}
.util-links{left:489px;top:13px;font-size:8px;color:var(--muted);display:flex;gap:20px}
.btn-signup,.btn-login{top:35px;height:16px;font-size:8px;font-weight:600;color:var(--white);display:flex;align-items:center;justify-content:center}
.btn-signup{left:507px;width:58px;background:var(--dark)}
.btn-login{left:570px;width:59px;background:var(--orange)}
/* nav */
.main-nav{left:0;top:63px;width:686px;height:28px;background:var(--dark);display:flex;padding-left:58px}
.main-nav a{display:flex;align-items:center;justify-content:center;height:28px;font-size:8px;font-weight:600;color:var(--white);text-decoration:none;border-right:1px solid #3e3330}
.main-nav a.active{background:var(--orange)}
/* hero */
.hero{left:0;top:91px;width:686px;height:333px;background:linear-gradient(90deg,#d9c79a 0%,#c9b384 30%,#7c5a45 55%,#6d4a38 70%,#c5b07c 100%)}
.hero-arrow{left:14px;top:243px}
.hero-panel{left:54px;top:196px;width:308px;height:143px;background:rgba(255,255,255,.72);text-align:center}
.hero-title{margin-top:18px;font-family:"Didact Gothic",sans-serif;font-size:20px;color:#222}
.hero-text{margin:7px 22px 0;font-family:"Roboto",sans-serif;font-size:7.6px;line-height:12.5px;color:#333}
.hero-actions{position:absolute;left:52px;top:100px;display:flex}
.hero-actions span{height:28px;display:flex;align-items:center;justify-content:center;font-family:"Roboto",sans-serif;font-size:9.5px;color:var(--white);background:var(--dark)}
.hero-actions .read{width:96px}
.hero-actions .gallery{width:96px;margin-left:5px}
.hero-or{position:absolute;left:89px;top:5px;width:18px;height:18px;border-radius:50%;background:var(--white);color:#222 !important;font-size:7px !important;font-style:italic;font-weight:500}
/* search */
.search-band{left:0;top:424px;width:686px;height:57px;background:var(--dark)}
.search-title{left:57px;top:440px;font-size:17px;color:var(--white)}
.field{top:443px;height:21px;background:var(--white);font-size:8px;color:#444;padding-left:7px;display:flex;align-items:center}
.field-category{left:185px;width:144px}
.field-caret{position:absolute;right:0;top:0;width:21px;height:21px;background:#3b3330;display:flex;align-items:center;justify-content:center}
.field-keyword{left:335px;width:142px}
.btn-search{left:486px;top:443px;width:143px;height:21px;background:var(--orange);color:var(--white);font-size:8px;display:flex;align-items:center;justify-content:center}
/* sections */
.section-title{left:0;width:686px;text-align:center;font-size:13.5px;color:#222}
.about-text{left:60px;top:522px;width:566px;text-align:center;font-size:7.6px;line-height:11px;color:#444}
.btn-more{left:307px;top:581px;width:72px;height:15px;background:var(--dark);color:var(--white);font-size:7.5px;display:flex;align-items:center;justify-content:center}
.circle-arrow{width:14px;height:14px}
/* listings */
.listing-card{top:662px;width:132px;height:230px;background:var(--white);border:1px solid var(--line);box-shadow:1px 2px 3px rgba(0,0,0,.12);text-align:center}
.listing-photo{height:168px}
.listing-name{margin-top:7px;font-size:10px;color:#555}
.listing-price{margin-top:3px;font-size:10.5px;color:var(--orange)}
.listing-place{margin-top:3px;font-size:6.8px;color:#444}
.view-badge{position:absolute;left:47px;top:64px;width:38px;height:38px;border-radius:50%;background:var(--white);display:flex;align-items:center;justify-content:center}
/* blog */
.blog-photo{top:967px;width:81px;height:84px}
.blog-body{top:967px;width:175px}
.blog-title{font-size:7.8px;font-weight:600;color:#222;line-height:10px}
.blog-text{margin-top:6px;font-size:6.6px;line-height:8.4px;color:#444}
.blog-meta{position:absolute;top:75px;left:0;display:flex;gap:4px}
.blog-meta span{height:10px;font-size:5.2px;font-weight:700;color:var(--white);display:flex;align-items:center;padding:0 7px}
.meta-date{background:var(--dark)}
.meta-count{background:var(--teal)}
.meta-more{background:var(--dark)}
/* footer */
.site-footer{left:0;top:1109px;width:686px;height:91px;background:var(--dark)}
.footer-links{left:0;top:1129px;width:686px;text-align:center;font-size:8px;font-weight:600;color:var(--white)}
.footer-links i{font-style:normal;margin:0 5px}
.copyright{left:0;top:1147px;width:686px;text-align:center;font-size:7px;color:var(--white)}
.social{top:1169px;width:18px;height:18px;border-radius:50%;background:var(--orange)}
</style>
</head>
<body>

<header class="site-header abs">
  <div class="brand abs"><span class="brand-dot"></span>SADDLEWEND</div>
  <div class="util-links abs"><span>My Account</span><span>|</span><span>Sell Your Horse</span></div>
  <div class="btn-signup abs">Signup</div>
  <div class="btn-login abs">Login</div>
</header>

<nav class="main-nav abs">
  <a class="active" style="width:94px">Home</a>
  <a style="width:95px">About Us</a>
  <a style="width:74px">Service</a>
  <a style="width:116px">Premium Listings</a>
  <a style="width:74px">Gallery</a>
  <a style="width:78px;border-right:none">Contact Us</a>
</nav>

<section class="hero abs" role="img" aria-label="Close-up photo of a brown and white paint horse in a sunlit grassy field"></section>
<svg class="hero-arrow abs" width="22" height="22" viewBox="0 0 22 22"><circle cx="11" cy="11" r="10" fill="none" stroke="#fff" stroke-opacity=".7" stroke-width="1.5"/><path d="M15 11H7M10 8l-3 3 3 3" fill="none" stroke="#fff" stroke-opacity=".8" stroke-width="1.5"/></svg>
<div class="hero-panel abs">
  <h1 class="hero-title">Saddlewend</h1>
  <p class="hero-text">Curabitur lobortis libero a rutrum tristique. Cras ipsum mauris, porttitor eu pulvinar sit amet, sollicitudin nec lectus. Sed lorem justo, ullamcorper malesuada porta non, vehicula sed lacus.</p>
  <div class="hero-actions">
    <span class="read">Read More</span>
    <span class="hero-or">or</span>
    <span class="gallery">VIEW GALLERY</span>
  </div>
</div>

<section class="search-band abs"></section>
<div class="search-title abs">Search Horse</div>
<div class="field field-category abs">Category<span class="field-caret"><svg width="8" height="5" viewBox="0 0 8 5"><path d="M0 0h8L4 5z" fill="#fff"/></svg></span></div>
<div class="field field-keyword abs">Keyword</div>
<div class="btn-search abs">Search Now</div>

<h2 class="section-title abs" style="top:497px">ABOUT US</h2>
<p class="about-text abs">Our company caters to the Australian Stock Horse, Quarter Horse and Paint Horse breeds of horse used for performance events such as Camp drafting and Cutting.Sed non sollicitudin dui. Aenean commodo odio nisl, scelerisque volutpat est ornare in. Sed placerat rhoncus laoreet. Aenean laoreet elit arcu, ut dignissim leo fermentum id. Etiam justo neque, semper a pretium vel, malesuada ac ex. Curabitur vel neque consectetur, imperdiet tortor eget, convallis ligula. Proin ornare urna ligula, ut placerat massa tempus vitae. Nunc accumsan placerat libero,</p>
<div class="btn-more abs">Read More</div>

<h2 class="section-title abs" style="top:629px">OUR PREMIUM LISTINGS</h2>
<svg class="circle-arrow abs" style="left:57px;top:629px" viewBox="0 0 14 14"><circle cx="7" cy="7" r="6.2" fill="none" stroke="#999" stroke-width="1"/><path d="M10 7H4M6 5L4 7l2 2" fill="none" stroke="#999" stroke-width="1"/></svg>
<svg class="circle-arrow abs" style="left:617px;top:629px" viewBox="0 0 14 14"><circle cx="7" cy="7" r="6.2" fill="none" stroke="#222" stroke-width="1.2"/><path d="M4 7h6M8 5l2 2-2 2" fill="none" stroke="#222" stroke-width="1.2"/></svg>

<article class="listing-card abs" style="left:58px">
  <div class="listing-photo" role="img" aria-label="Photo of a dark bay horse galloping at dusk" style="background:linear-gradient(180deg,#5a4a40,#6e5a4c 60%,#8a7563);position:relative">
    <span class="view-badge"><svg width="20" height="12" viewBox="0 0 20 12"><path d="M1 6C4 1 16 1 19 6 16 11 4 11 1 6z" fill="#222"/><circle cx="10" cy="6" r="3" fill="#fff"/><circle cx="10" cy="6" r="1.6" fill="#222"/></svg></span>
  </div>
  <p class="listing-name">Lorem ipsum Dolor</p><p class="listing-price">$3892.29</p><p class="listing-place">Contantry popilar sit</p>
</article>
<article class="listing-card abs" style="left:205px">
  <div class="listing-photo" role="img" aria-label="Photo of a bay horse trotting in a sandy yard" style="background:linear-gradient(180deg,#b9bba8,#9a6b45 55%,#c29a7a)"></div>
  <p class="listing-name">Lorem ipsum Dolor</p><p class="listing-price">$3892.29</p><p class="listing-place">Contantry popilar sit</p>
</article>
<article class="listing-card abs" style="left:351px">
  <div class="listing-photo" role="img" aria-label="Photo of a chestnut horse with bridle against a pale background" style="background:linear-gradient(135deg,#e9e6c4,#8a3d22 50%,#e7e3c0)"></div>
  <p class="listing-name">Lorem ipsum Dolor</p><p class="listing-price">$3892.29</p><p class="listing-place">Contantry popilar sit</p>
</article>
<article class="listing-card abs" style="left:497px">
  <div class="listing-photo" role="img" aria-label="Photo of a buckskin horse running in a desert" style="background:linear-gradient(180deg,#e5d6bb,#b9a88c 55%,#d9c7a8)"></div>
  <p class="listing-name">Lorem ipsum Dolor</p><p class="listing-price">$3892.29</p><p class="listing-place">Contantry popilar sit</p>
</article>

<h2 class="section-title abs" style="top:926px">LATEST BLOG</h2>
<svg class="circle-arrow abs" style="left:57px;top:927px" viewBox="0 0 14 14"><circle cx="7" cy="7" r="6.2" fill="none" stroke="#999" stroke-width="1"/><path d="M10 7H4M6 5L4 7l2 2" fill="none" stroke="#999" stroke-width="1"/></svg>
<svg class="circle-arrow abs" style="left:617px;top:927px" viewBox="0 0 14 14"><circle cx="7" cy="7" r="6.2" fill="none" stroke="#222" stroke-width="1.2"/><path d="M4 7h6M8 5l2 2-2 2" fill="none" stroke="#222" stroke-width="1.2"/></svg>

<div class="blog-photo abs" style="left:58px;background:linear-gradient(180deg,#6e4a3a,#c07a45 60%,#5c6a2a)" role="img" aria-label="Photo of a dark horse galloping under a sunset sky"></div>
<article class="blog-body abs" style="left:150px">
  <h3 class="blog-title">Brindlecote Financial Group Participating in the 2014 Ridgeway Golf Tournament</h3>
  <p class="blog-text">mollis varius dolor id, varius molestie urna. Cras id tellus nisl. Fusce purus ante, elementum id metus eget, congue pharetra dolor. Sed non mollis quam. Nulla non eros diam.</p>
  <div class="blog-meta"><span class="meta-date">05 june 15</span><span class="meta-count">12</span><span class="meta-more">Read More</span></div>
</article>

<div class="blog-photo abs" style="left:361px;background:linear-gradient(90deg,#1a1a1a,#6a6a6a 50%,#222)" role="img" aria-label="Photo of three horses side by side on a black background"></div>
<article class="blog-body abs" style="left:453px">
  <h3 class="blog-title">New Product: Foreign Exchange</h3>
  <p class="blog-text">mollis varius dolor id, varius molestie urna. Cras id tellus nisl. Fusce purus ante, elementum id metus eget, congue pharetra dolor. Sed non mollis quam. Nulla non eros diam. Proin ultricies, felis eget sceler­isque</p>
  <div class="blog-meta"><span class="meta-date">05 june 15</span><span class="meta-count">12</span><span class="meta-more">Read More</span></div>
</article>

<footer class="site-footer abs"></footer>
<div class="footer-links abs">Home<i>|</i>About Us<i>|</i>Service<i>|</i>Premium Listings<i>|</i>Gallery<i>|</i>Contact Us</div>
<div class="copyright abs">Copyright(c) website name. Allrights Reserved</div>
<span class="social abs" style="left:310px" aria-label="Social link"></span>
<span class="social abs" style="left:333px" aria-label="Social link"></span>
<span class="social abs" style="left:355px" aria-label="Social link"></span>

</body>
</html>
```